RW Framewell Inc Business cards

We need business cards using our existing logo but slightly modified. Right now the logo says RW Loadbearing Masonry. We want to keep the RW part of the design, but replace the Structural Concrete portion with "FRAMEWELL". Please see the attached file.
Ideally this would be a blank template so we can add Different Names, titles, and phone numbers later.
On the one side we want only the logo and on the other side the detail. I'm attaching an example for you to see.
Please reach out with any other questions. Our address and other details will be given out once we find a design we like.

Target Market(s)

Construction Industry

```html
<!DOCTYPE html>
<html lang="en">
<head>
<meta charset="utf-8">
<title>RW Framewell Inc Business Cards</title>
<link rel="stylesheet" href="https://fonts.googleapis.com/css2?family=Montserrat:wght@500;600;700&family=Roboto:wght@400;500&display=swap">
<style>
  :root {
    --backdrop: #6c8dc4;
    --brand-blue: #2f5fa3;
    --brand-blue-deep: #23508f;
    --emboss-blue: #1f4c8c;
    --accent-grey: #6d6e71;
    --paper: #f3f3f3;
    --ink-light: #ffffff;
    --logo-blue: #2a5aa0;
  }
  * { box-sizing: border-box; margin: 0; padding: 0; }
  html, body {
    width: 1200px; height: 852px; overflow: hidden;
    background: var(--backdrop);
  }
  .sheet {
    position: relative; width: 1200px; height: 852px;
    display: flex; align-items: center; justify-content: center; gap: 44px;
  }
  .card {
    position: relative; width: 510px; height: 292px;
    border-radius: 22px; overflow: hidden;
    box-shadow: 0 6px 18px rgba(20, 40, 80, 0.25);
  }
  .card-front {
    background: var(--brand-blue);
    display: flex; align-items: center; justify-content: center;
  }
  .wordmark {
    font-family: "Montserrat", sans-serif; font-weight: 700;
    text-align: center; line-height: 1;
  }
  .wordmark .initials { display: block; font-size: 92px; letter-spacing: 2px; }
  .wordmark .name { display: block; font-size: 27px; letter-spacing: 7px; margin-top: 6px; }
  .card-front .wordmark { color: var(--emboss-blue); }

  .card-back { background: var(--paper); }
  .card-back .shape { position: absolute; inset: 0; width: 100%; height: 100%; }
  .card-back .wordmark {
    position: absolute; left: 30px; top: 120px; width: 220px;
    color: var(--logo-blue);
  }
  .card-back .wordmark .initials { font-size: 64px; }
  .card-back .wordmark .name { font-size: 19px; letter-spacing: 5px; }

  .details {
    position: absolute; left: 300px; top: 52px; width: 200px;
    color: var(--ink-light); font-family: "Roboto", sans-serif;
  }
  .person { font-family: "Montserrat", sans-serif; font-weight: 700; font-size: 19px; }
  .role { font-size: 12px; margin-top: 3px; margin-left: 12px; }
  .contact-list { list-style: none; margin-top: 20px; font-size: 12px; line-height: 1.5; }
  .contact-list li { display: flex; align-items: flex-start; gap: 8px; margin-bottom: 5px; }
  .contact-list svg { width: 11px; height: 11px; flex: none; margin-top: 3px; }
</style>
</head>
<body>
<main class="sheet">
  <section class="card card-front" aria-label="Card front">
    <div class="wordmark">
      <span class="initials">RW</span>
      <span class="name">FRAMEWELL</span>
    </div>
  </section>

  <section class="card card-back" aria-label="Card back">
    <svg class="shape" viewBox="0 0 510 292" preserveAspectRatio="none" aria-hidden="true">
      <path d="M0 0 H510 V292 H0 Z" fill="var(--paper)"/>
      <path d="M200 0 Q300 120 268 292 H510 V0 Z" fill="var(--accent-grey)"/>
      <path d="M214 0 Q314 120 282 292 H510 V0 Z" fill="var(--brand-blue)"/>
    </svg>

    <div class="wordmark">
      <span class="initials">RW</span>
      <span class="name">FRAMEWELL</span>
    </div>

    <div class="details">
      <p class="person">Dan RW Miller</p>
      <p class="role">Managing Director</p>
      <ul class="contact-list">
        <li>
          <svg viewBox="0 0 12 12" aria-hidden="true"><path d="M3 1 L5 3.5 L4 5 Q5 7 7 8 L8.5 7 L11 9 L10 11 Q4 11 1 2 Z" fill="#fff"/></svg>
          <span>555-014-2270</span>
        </li>
        <li>
          <svg viewBox="0 0 12 12" aria-hidden="true"><rect x="1" y="3" width="10" height="7" fill="none" stroke="#fff" stroke-width="1.2"/><path d="M1 3 L6 7 L11 3" fill="none" stroke="#fff" stroke-width="1.2"/></svg>
          <span>dan@framewellsite.com</span>
        </li>
        <li>
          <svg viewBox="0 0 12 12" aria-hidden="true"><circle cx="6" cy="6" r="4.8" fill="none" stroke="#fff" stroke-width="1.1"/><path d="M1.2 6 H10.8 M6 1.2 Q3 6 6 10.8 M6 1.2 Q9 6 6 10.8" fill="none" stroke="#fff" stroke-width="0.9"/></svg>
          <span>www.framewellsite.com</span>
        </li>
        <li>
          <svg viewBox="0 0 12 12" aria-hidden="true"><path d="M6 11 Q2 6.5 2 4.5 A4 4 0 0 1 10 4.5 Q10 6.5 6 11 Z" fill="#fff"/><circle cx="6" cy="4.6" r="1.4" fill="var(--brand-blue)"/></svg>
          <span>87 Millbrook Rd., Fairview,<br>Oregon, US 970245</span>
        </li>
      </ul>
    </div>
  </section>
</main>
</body>
</html>
```